VFX Company Business Card Design Project

The Kestrel Works is a decentralized Visual Effects Studio servicing the television and feature film industries.
Project Brief:
Take our logo that was previously designed on Pencil Harbor and make a double sided business card.
Requirements:
- Card MUST be double sided.
- Front of card MUST have the yellow part of our logo against the dark grey background.
- Back of card is completely up to the designer.
- Back of card must include the complete company logo.
Please follow these File Preparation guidelines:
http://printnook.ca/infopage?file=filetype_en&s=PrintNook_new&lang=en
Business

```html
<!DOCTYPE html>
<html lang="en">
<head>
<meta charset="utf-8">
<title>The Kestrel Works – Business Cards</title>
<link rel="stylesheet" href="https://fonts.googleapis.com/css2?family=Montserrat:wght@400;600&family=Source+Sans+3:wght@400;600&display=swap">
<style>
  :root {
    --backdrop: #d9d6d1;
    --card: #2b2b2b;
    --gold: #f2c43d;
    --ivory: #eef2e6;
    --slate: #6b7073;
    --metal-dark: #151515;
    --metal-mid: #3a3a3a;
    --band: #eef1e6;
    --band-text: #2b2b2b;
  }
  * { margin: 0; padding: 0; box-sizing: border-box; }
  html, body { width: 1200px; height: 727px; overflow: hidden; }
  body { background: var(--backdrop); position: relative; font-family: "Montserrat", sans-serif; }

  .card {
    position: absolute;
    width: 525px;
    height: 300px;
    border-radius: 28px;
    background: var(--card);
    overflow: hidden;
  }
  .card--front   { left: 68px;  top: 43px; }
  .card--contact { left: 626px; top: 48px; background: linear-gradient(105deg, var(--metal-dark) 0%, var(--metal-mid) 45%, #4a4a4a 60%, var(--metal-dark) 100%); }
  .card--combo   { left: 65px;  top: 384px; }
  .card--wordmark{ left: 623px; top: 388px; }

  /* Front: name in gold with one plain circle */
  .front-mark {
    position: absolute; inset: 0;
    display: flex; align-items: center; justify-content: center; gap: 18px;
    color: var(--gold); font-weight: 600; font-size: 40px; letter-spacing: 1px;
  }
  .mark-dot { width: 26px; height: 26px; border-radius: 50%; background: var(--gold); flex: none; }

  /* Company name + tagline lockup */
  .lockup { display: flex; flex-direction: column; align-items: flex-start; }
  .lockup__name { color: var(--ivory); font-weight: 600; line-height: 1; white-space: nowrap; }
  .lockup__tagline { color: var(--slate); font-weight: 400; text-transform: uppercase; white-space: nowrap; }

  /* Contact card */
  .contact-lockup { position: absolute; left: 44px; top: 126px; }
  .contact-lockup .lockup__name { font-size: 21px; }
  .contact-lockup .lockup__tagline { font-size: 12px; letter-spacing: 4.6px; margin-top: 4px; }
  .contact-divider {
    position: absolute; left: 292px; top: 58px; width: 2px; height: 170px;
    background: linear-gradient(to bottom, transparent, #9a9a9a 30%, #d8d8d8 55%, #9a9a9a 75%, transparent);
  }
  .contact-details {
    position: absolute; left: 309px; top: 76px;
    font-family: "Source Sans 3", sans-serif; color: var(--ivory);
  }
  .contact-details__name { font-size: 19px; font-weight: 600; }
  .contact-details__title { font-size: 15px; margin-bottom: 12px; }
  .contact-details__line { font-size: 13.5px; line-height: 21px; }
  .contact-band {
    position: absolute; left: 0; bottom: 0; width: 100%; height: 30px;
    background: var(--band); color: var(--band-text);
    font-family: "Source Sans 3", sans-serif; font-size: 13.5px;
    display: flex; align-items: center; justify-content: center;
  }

  /* Combo card */
  .combo-lockup {
    position: absolute; left: 38px; top: 108px;
    display: flex; align-items: center; gap: 20px;
  }
  .combo-lockup .mark-dot { width: 44px; height: 44px; }
  .combo-lockup .lockup__name { font-size: 30px; }
  .combo-lockup .lockup__tagline { font-size: 12.5px; letter-spacing: 5.4px; margin-top: 6px; }

  /* Wordmark card */
  .wordmark-lockup { position: absolute; left: 58px; top: 96px; }
  .wordmark-lockup .lockup__name { font-size: 44px; }
  .wordmark-lockup .lockup__tagline { font-size: 19px; letter-spacing: 9.4px; margin-top: 10px; }

  .card-url {
    position: absolute; left: 0; bottom: 24px; width: 100%;
    text-align: center; color: var(--ivory);
    font-size: 16px; letter-spacing: 2.6px;
  }
</style>
</head>
<body>

  <section class="card card--front" aria-label="Card front">
    <div class="front-mark"><span class="mark-dot"></span>The Kestrel Works</div>
  </section>

  <section class="card card--contact" aria-label="Card back with contact details">
    <div class="lockup contact-lockup">
      <span class="lockup__name">The Kestrel Works</span>
      <span class="lockup__tagline">Virtual Studio</span>
    </div>
    <div class="contact-divider"></div>
    <div class="contact-details">
      <p class="contact-details__name">Your Name</p>
      <p class="contact-details__title">Title</p>
      <p class="contact-details__line">P: 0123 456789</p>
      <p class="contact-details__line">F: 0123 456789</p>
      <p class="contact-details__line">E: info@kestrelworks.com</p>
      <p class="contact-details__line">W: www.kestrelworks.com</p>
    </div>
    <div class="contact-band">12, Harbor Court, Easton, State 0718</div>
  </section>

  <section class="card card--combo" aria-label="Card back with full logo">
    <div class="combo-lockup">
      <span class="mark-dot"></span>
      <div class="lockup">
        <span class="lockup__name">The Kestrel Works</span>
        <span class="lockup__tagline">Virtual Studio</span>
      </div>
    </div>
    <p class="card-url">www.kestrelworks.com</p>
  </section>

  <section class="card card--wordmark" aria-label="Card back with wordmark">
    <div class="lockup wordmark-lockup">
      <span class="lockup__name">The Kestrel Works</span>
      <span class="lockup__tagline">Virtual Studio</span>
    </div>
    <p class="card-url">www.kestrelworks.com</p>
  </section>

</body>
</html>
```